Human Resource Consulting practice needs a business card design

We need a business card design (double sided colour) for our Human Resource (HR) consulting practice in regional New South Wales, australia. Our business name is Staff Compass. We support small and medium business across the Mid North Coast of New South Wales by providing them with outsourced HR support, services and products to help them achieve compliance with workplace legislation and across all areas of the employment lifecycle from recruitment to termination and everything in between. Our corporate colours are hot pink and black. The final design should communicate professionalism, trust, people focus.
I have attached the current (old) business card for your reference.

Target Market(s)

Business owners and high level managers

Industry/Entity Type

Business

Contact Information for Business Card

Name
Title
Phone no
Mobile no
Address
PO Box
email address
website

Colors
e34197

Requirements
Must have
• Tempate for changing business card personal details including Name, position title, mobile number, email address.
• Keep current logo and colours as per attached
• Logo must be presented in 2 colours or black only not white
Nice to have
• One side logo and graphic only other side logo and personal details
Should not have
• Should not be the same as the current version (attached) but a modern interpretation.
• Does not need a busy reverse side with our list of services as per current version. I feel this is too busy.
• No photos

```html
<!DOCTYPE html>
<html lang="en">
<head>
<meta charset="utf-8">
<title>Staff Compass – Business Card</title>
<link rel="stylesheet" href="https://fonts.googleapis.com/css2?family=Lato:wght@400;700&display=swap">
<style>
  :root {
    --hot-pink: #e34197;
    --pink-deep: #d02a86;
    --ink: #111111;
    --ink-soft: #2a2a2a;
    --paper: #ffffff;
    --mist: #e6e6e6;
    --text-grey: #3c3c3c;
    --backdrop: #ececec;
  }
  * { box-sizing: border-box; margin: 0; padding: 0; }
  html, body {
    width: 1200px; height: 1023px; overflow: hidden;
    background: var(--backdrop);
    font-family: "Lato", Arial, sans-serif;
  }
  .sheet {
    position: relative; width: 1200px; height: 1023px;
  }
  .card {
    position: absolute; left: 250px; width: 700px; height: 427px;
    border-radius: 22px; overflow: hidden;
    box-shadow: 0 10px 30px rgba(0,0,0,0.18);
  }
  .card--front { top: 60px; background: var(--paper); }
  .card--back { top: 536px; background: linear-gradient(160deg, var(--ink-soft) 0%, var(--ink) 60%); }

  .swoosh { position: absolute; inset: 0; width: 100%; height: 100%; }

  .brand {
    position: absolute; display: flex; align-items: center; gap: 10px;
    font-weight: 700; color: var(--hot-pink); white-space: nowrap;
  }
  .brand__dot {
    width: 14px; height: 14px; border-radius: 50%; background: var(--hot-pink);
  }
  .card--front .brand { left: 60px; top: 150px; font-size: 44px; }

  .contact {
    position: absolute; right: 44px; top: 40px; text-align: right;
    color: var(--text-grey); font-size: 17px; line-height: 1.45;
  }
  .contact__name { color: var(--hot-pink); font-weight: 700; font-size: 21px; }
  .contact__title { margin-bottom: 14px; }
  .contact__line { display: flex; justify-content: flex-end; align-items: center; gap: 8px; }
  .contact__line svg { width: 15px; height: 15px; flex: none; }
  .contact__gap { margin-top: 12px; }

  .card--back .brand { left: 70px; top: 110px; font-size: 66px; gap: 14px; }
  .card--back .brand__dot { width: 20px; height: 20px; }
  .website {
    position: absolute; left: 74px; top: 205px;
    color: #d8d8d8; font-size: 18px; letter-spacing: 0.3px;
  }
  .star-field {
    position: absolute; right: 0; bottom: 0; width: 380px; height: 300px;
    background: linear-gradient(135deg, rgba(227,65,151,0.15) 0%, rgba(227,65,151,0.75) 70%, var(--hot-pink) 100%);
    clip-path: polygon(100% 0, 100% 100%, 0 100%);
  }
</style>
</head>
<body>
<main class="sheet">

  <section class="card card--front" aria-label="Business card front">
    <svg class="swoosh" viewBox="0 0 700 427" preserveAspectRatio="none" aria-hidden="true">
      <path d="M0,290 C260,400 540,360 700,220 L700,427 L0,427 Z" fill="var(--hot-pink)"/>
      <path d="M0,350 C270,450 560,400 700,290 L700,322 C560,432 270,472 0,388 Z" fill="var(--mist)"/>
      <path d="M0,290 C260,400 540,360 700,220 L700,236 C540,378 260,414 0,304 Z" fill="var(--pink-deep)" opacity="0.5"/>
    </svg>

    <div class="brand"><span class="brand__dot"></span>Staff Compass</div>

    <div class="contact">
      <p class="contact__name">Claire Morton</p>
      <p class="contact__title">Principal Consultant</p>
      <p class="contact__line">02 6500 1234
        <svg viewBox="0 0 16 16" aria-hidden="true"><path d="M4 1h3l1 4-2 1.5a9 9 0 0 0 3.5 3.5L11 8l4 1v3c0 1-1 2-2 2A12 12 0 0 1 2 3c0-1 1-2 2-2z" fill="var(--hot-pink)"/></svg>
      </p>
      <p class="contact__line">0400 555 812
        <svg viewBox="0 0 16 16" aria-hidden="true"><rect x="4" y="1" width="8" height="14" rx="1.5" fill="none" stroke="var(--hot-pink)" stroke-width="1.6"/><circle cx="8" cy="12.5" r="0.9" fill="var(--hot-pink)"/></svg>
      </p>
      <p class="contact__line contact__gap">claire@staffcompass.com.au
        <svg viewBox="0 0 16 16" aria-hidden="true"><rect x="1" y="3" width="14" height="10" fill="var(--hot-pink)"/><path d="M1 3l7 6 7-6" fill="none" stroke="#fff" stroke-width="1.3"/></svg>
      </p>
      <p class="contact__gap">P.O. Box 108, Harbourton</p>
      <p>NSW 2400</p>
    </div>
  </section>

  <section class="card card--back" aria-label="Business card back">
    <div class="brand"><span class="brand__dot"></span>Staff Compass</div>
    <p class="website">www.staffcompass.com.au</p>
    <div class="star-field" role="img" aria-label="Decorative field of pink stars fading into the corner"></div>
  </section>

</main>
</body>
</html>
```